Kelvara Pools

Luxury pool designer builder brochure

Company name is "Kelvara"
Tag line is "Pools for the Mind Body & Soul"
Maybe integrate "Luxury Urban Lifestyle"

Target Market(s)

30 to 65 income of 200000.00 plus Affluent, high end life style
Luxury living

Industry/Entity Type

It Company

Font styles to use
Serif

Colors
000000

Requirements
Must have
• NOTE:
• Please remove the "Aquatic environments for the under the logo.
• I want a black background with a very contemporary feel.
• This is a luxury lifestyle product.

```html
<!DOCTYPE html>
<html lang="en">
<head>
<meta charset="utf-8">
<title>Kelvara Pools — Brochure</title>
<link href="https://fonts.googleapis.com/css2?family=Bodoni+Moda:opsz,wght@6..96,400&display=swap" rel="stylesheet">
<style>
  :root {
    --ink: #000000;
    --paper: #f3f3f3;
    --white: #ffffff;
    --stage: #e2e2e2;
    --fold: #1a1a1a;
    --caption: #111111;
  }
  * { box-sizing: border-box; margin: 0; padding: 0; }
  html, body { width: 1200px; height: 849px; overflow: hidden; }
  body {
    background: var(--stage);
    font-family: "Bodoni Moda", "Didot", serif;
    display: flex;
    align-items: center;
    justify-content: center;
    gap: 40px;
  }
  .spread {
    display: flex;
    width: 560px;
    height: 396px;
    box-shadow: 0 10px 30px rgba(0,0,0,0.15);
  }
  .page {
    position: relative;
    width: 280px;
    height: 396px;
    overflow: hidden;
  }
  .page--dark { background: var(--ink); color: var(--white); }
  .page--dark + .page--dark { border-left: 1px solid var(--fold); }
  .page--light { background: var(--paper); color: var(--caption); }

  .tagline {
    position: absolute;
    right: 26px;
    top: 140px;
    text-align: right;
    font-size: 15px;
    line-height: 1.15;
    letter-spacing: 0.02em;
  }
  .brand {
    position: absolute;
    right: 22px;
    bottom: 20px;
    font-size: 11px;
    letter-spacing: 0.12em;
  }
  .address {
    position: absolute;
    left: 34px;
    bottom: 40px;
    font-size: 6px;
    letter-spacing: 0.06em;
    color: #cfcfcf;
  }

  .photo { display: block; width: 100%; }
  .photo--estate {
    height: 198px;
    background: linear-gradient(180deg, #7f8da0 0%, #a7a7a0 40%, #c98c5c 62%, #3f8fb8 82%, #6d8a4a 100%);
  }
  .photo--poolside {
    height: 198px;
    background: linear-gradient(180deg, #6f7f93 0%, #9b8f82 35%, #d07a3a 55%, #2f6e96 78%, #b9b2a6 100%);
  }

  .gallery {
    position: absolute;
    top: 62px;
    left: 50%;
    transform: translateX(-50%);
    display: flex;
    flex-direction: column;
    gap: 10px;
  }
  .thumb { width: 84px; height: 58px; }
  .thumb--patio { background: linear-gradient(160deg, #8aa0b0 0%, #b0784a 50%, #3b8fb0 100%); }
  .thumb--lagoon { background: linear-gradient(160deg, #c9d2cf 0%, #4aa6c4 55%, #6b8a50 100%); }
  .thumb--evening { background: linear-gradient(160deg, #3c4d62 0%, #d38a3a 55%, #2e6f9a 100%); }

  .lifestyle {
    position: absolute;
    left: 0;
    right: 0;
    bottom: 48px;
    text-align: center;
    font-size: 11px;
    letter-spacing: 0.04em;
  }
</style>
</head>
<body>
  <section class="spread spread--outer" aria-label="Brochure outer spread">
    <div class="page page--dark page--back">
      <p class="address">address</p>
    </div>
    <div class="page page--dark page--front">
      <h1 class="tagline">Pools for the Mind<br>Body &amp; Soul</h1>
      <p class="brand">Kelvara</p>
    </div>
  </section>

  <section class="spread spread--inner" aria-label="Brochure inner spread">
    <div class="page page--photo">
      <div class="photo photo--estate" role="img" aria-label="Luxury villa with infinity pool at dusk"></div>
      <div class="photo photo--poolside" role="img" aria-label="Poolside fire bowl and infinity edge pool at dusk"></div>
    </div>
    <div class="page page--light">
      <div class="gallery">
        <div class="thumb thumb--patio" role="img" aria-label="Pool terrace with paved patio"></div>
        <div class="thumb thumb--lagoon" role="img" aria-label="Garden pool with blue water and greenery"></div>
        <div class="thumb thumb--evening" role="img" aria-label="Evening pool with palm and lights"></div>
      </div>
      <p class="lifestyle">Luxury Urban Lifestyle</p>
    </div>
  </section>
</body>
</html>
```